4747 5858

Web(re)design of an existing directory search site www.le5858.be (in Dutch www.de4747.be and in English www.3838.be).

This site is a directory site, i.e. a "white pages" site whereby people can search the phone & details of another person based on a combination of name + city (for instance smith in Brussels); one can also search a company also based on a combination of name + city (for instance Vornak in Brussels); last but not least one can also search the name of the subscriber behind a specific telephone number (also called reverse search).

This site is quite outdated and needs a redesign, see instructions.

We need the output in XD format.

```html
<!DOCTYPE html>
<html lang="en">
<head>
<meta charset="utf-8">
<title>38-38 Web Redesign Presentation</title>
<link href="https://fonts.googleapis.com/css2?family=Roboto:wght@400;500;700&family=Saira:wght@500;600;700&display=swap" rel="stylesheet">
<style>
:root{
  --red:#d91f26;
  --red-soft:#ef4a50;
  --pink:#fde8ea;
  --board:#f4f4f5;
  --ink:#222;
  --muted:#6b6b6b;
  --line:#bdbdbd;
  --foot:#f6f6f6;
  --table:#efefef;
  --link:#2a6cd6;
}
*{box-sizing:border-box;margin:0;padding:0}
html,body{width:1200px;height:1200px;overflow:hidden;background:var(--board);font-family:'Roboto',sans-serif;color:var(--ink)}
.board{position:absolute;left:0;top:0;width:1932px;height:1932px;transform:scale(.62112);transform-origin:0 0;background:var(--board)}
.abs{position:absolute}
.intro,.outro{position:absolute;left:0;width:1932px;text-align:center;color:var(--red);font-weight:500;font-size:38px;line-height:45px}
.intro{top:78px}
.outro{top:1684px}
.caption{position:absolute;font-size:12.5px;line-height:17px;color:var(--muted);text-align:center}

.screen{position:absolute;width:585px;background:#fff;border-radius:9px;overflow:hidden;box-shadow:0 4px 14px rgba(0,0,0,.12)}
.navbar{position:absolute;left:0;top:0;width:100%;height:38px;background:var(--red);z-index:3}
.brand{position:absolute;left:40px;top:3px;font-family:'Saira',sans-serif;font-weight:700;font-size:25px;line-height:32px;color:#fff;letter-spacing:.5px}
.nav-links{position:absolute;top:14px;display:flex;gap:16px;font-size:8px;color:#fde0e0}
.nav-links span.active{color:#fff;font-weight:700;border-bottom:1.5px solid #fff;padding-bottom:3px}
.lang{position:absolute;left:495px;top:10px;width:77px;height:14px;border:1px solid #f3a3a6;border-radius:2px;font-size:6.5px;color:#fff;display:flex;align-items:center;padding-left:18px;gap:4px}
.lang i{display:inline-block;width:8px;height:5px;background:#f3b7ba}
.lang b{font-weight:400;margin-left:6px}

.hero{position:absolute;left:0;top:38px;width:100%;height:192px;background:var(--pink)}
.hero-art{position:absolute;left:0;top:50px;width:270px;height:155px;border-radius:40% 55% 10% 10%;background:linear-gradient(100deg,#f08a8e 0%,#d93a40 35%,#fbd0d3 60%,#b9c6ee 80%,#6f86d6 100%)}
.hero-title{position:absolute;left:292px;top:50px;font-family:'Saira',sans-serif;font-weight:500;font-size:17.5px;line-height:22px;color:var(--red)}
.hero-sub{position:absolute;left:292px;top:104px;font-size:8.5px;color:var(--red)}
.search-card{position:absolute;left:292px;top:125px;width:263px;height:88px;background:#fff;border-radius:3px}
.search-card.short{height:63px}
.field{position:absolute;height:14px;border:1px solid var(--line);border-radius:2px;font-size:5.5px;color:#aaa;padding:3px 4px;background:#fff}
.field.filled{color:var(--ink);border-color:#888;background:#f7f7f7}
.field .clear{position:absolute;right:4px;top:3px;width:7px;height:7px}
.btn{position:absolute;height:16px;background:var(--red-soft);border-radius:2px;color:#fff;font-size:6.5px;display:flex;align-items:center;justify-content:center;gap:5px}
.btn svg{width:8px;height:8px}

.about{position:absolute;left:0;width:100%;text-align:center}
.about h3{font-size:10px;font-weight:700;margin-bottom:13px}
.about p{width:390px;margin:0 auto;font-size:5.6px;line-height:9px}

.footer{position:absolute;left:0;bottom:0;width:100%;height:44px;background:var(--foot)}
.footer .copy{position:absolute;left:38px;bottom:6px;font-size:5px;color:#333}
.footer .legal{position:absolute;right:40px;bottom:6px;font-size:5px;color:#333}
.footer .mark{position:absolute;left:282px;top:14px;display:flex;align-items:center;gap:3px;font-size:6px;font-weight:700;color:#111}
.footer .mark i{display:block;width:7px;height:7px;border-radius:50%;background:var(--red)}

.found{position:absolute;left:0;width:100%;text-align:center;font-size:5.5px;color:#555}
.found b{color:var(--ink)}
.result{position:absolute;left:152px;width:281px;background:var(--table);padding:6px 8px;display:flex;flex-direction:column;gap:4px}
.result .row{display:flex;height:18.5px;background:#fff;align-items:center;font-size:7px}
.result .row span{width:62px;padding-left:4px;font-size:5px;color:#666;font-weight:500}
.result .row a{color:var(--link);text-decoration:underline}
.sticky{position:absolute;left:0;top:38px;width:100%;height:40px;background:var(--pink);z-index:2}

.intl-title{position:absolute;left:62px;top:105px;font-family:'Saira',sans-serif;font-weight:500;font-size:17.5px;line-height:22px;color:var(--red)}
.art{position:absolute;border-radius:46% 54% 40% 60%}
.intl-text{position:absolute;width:275px;font-size:7px;line-height:12.4px;color:#444}
.intl-band{position:absolute;left:0;top:627px;width:100%;height:342px;background:var(--pink)}
.intl-note{position:absolute;left:0;width:100%;text-align:center;color:var(--red)}
.map{position:absolute;left:167px;top:73px;width:232px;height:207px;background:radial-gradient(circle at 55% 45%,#f0a24a 0%,#e8b85a 28%,#9fbf86 55%,#efe6d2 78%);border:1px solid #d9d2c0}
</style>
</head>
<body>
<main class="board">

  <p class="intro">Hi sir, have a nice day.<br>Here are the results of my design for web redesign 58-58. I'm using version 38-38.<br>I hope you like it.</p>

  <p class="caption" style="left:64px;top:275px;width:585px">First is the landing page, I added a bit of information about what38-38 is in " What is 38-38?".</p>
  <p class="caption" style="left:680px;top:275px;width:585px">Next is the search results, for the search results table I made it simpler and a link for the location to the map service is also available. The search card will be responsive if you scroll down.</p>
  <p class="caption" style="left:1284px;top:275px;width:585px">Next is the international page, I give some illustrations so that users feel interested in using the 38-38 website.</p>
  <p class="caption" style="left:64px;top:739px;width:585px">Display of Companies page and Reverse Directory</p>

  <!-- People landing -->
  <section class="screen" style="left:64px;top:312px;height:388px">
    <header class="navbar">
      <div class="brand">38-38</div>
      <nav class="nav-links" style="left:281px"><span class="active">People</span><span>Companies</span><span>Reverse</span><span>International</span></nav>
      <div class="lang"><i></i>English<b>⌄</b></div>
    </header>
    <div class="hero"></div>
    <div class="hero-art" role="img" aria-label="Illustration of a phone directory and a delivery van with map pins"></div>
    <h2 class="hero-title">The ONE number for ALL<br>directory enquiries</h2>
    <p class="hero-sub">Find people, contact info &amp; background checks</p>
    <div class="search-card">
      <div class="field" style="left:12px;top:12px;width:116px">First Name</div>
      <div class="field" style="left:135px;top:12px;width:116px">Last Name</div>
      <div class="field" style="left:12px;top:37px;width:239px">Locality</div>
      <div class="btn" style="left:12px;top:61px;width:239px">38-38! <svg viewBox="0 0 10 10"><circle cx="5.5" cy="4.5" r="3.2" fill="none" stroke="#fff" stroke-width="1.2"/><line x1="3.2" y1="6.8" x2="1" y2="9" stroke="#fff" stroke-width="1.2"/></svg></div>
    </div>
    <div class="about" style="top:251px"><h3>What is 38-38?</h3><p>Lorem ipsum dolor sit amet, consectetur adipiscing elit, sed do eiusmod tempor incididunt ut labore et dolore magna aliqua. Ut enim ad minim veniam, quis nostrud exercitation ullamco laboris nisi ut aliquip ex ea commodo consequat. Duis aute irure dolor in reprehenderit in voluptate velit esse cillum dolore eu fugiat nulla pariatur.</p></div>
    <footer class="footer"><span class="copy">Copyright NORVELD 2010, all rights reserved &nbsp;|&nbsp; B2B Service</span><span class="mark"><i></i>www.4747.be</span><span class="legal">Help &nbsp;|&nbsp; Terms of Use &nbsp;|&nbsp; Respect for privacy</span></footer>
  </section>

  <!-- Companies -->
  <section class="screen" style="left:70px;top:775px;height:388px">
    <header class="navbar">
      <div class="brand">38-38</div>
      <nav class="nav-links" style="left:281px"><span>People</span><span class="active">Companies</span><span>Reverse</span><span>International</span></nav>
      <div class="lang"><i></i>English<b>⌄</b></div>
    </header>
    <div class="hero"></div>
    <div class="hero-art" role="img" aria-label="Illustration of a phone directory and a delivery van with map pins"></div>
    <h2 class="hero-title">The ONE number for ALL<br>directory enquiries</h2>
    <p class="hero-sub">Find by Company name</p>
    <div class="search-card">
      <div class="field" style="left:12px;top:12px;width:239px">Company Name</div>
      <div class="field" style="left:12px;top:37px;width:239px">Locality</div>
      <div class="btn" style="left:12px;top:61px;width:239px">38-38! <svg viewBox="0 0 10 10"><circle cx="5.5" cy="4.5" r="3.2" fill="none" stroke="#fff" stroke-width="1.2"/><line x1="3.2" y1="6.8" x2="1" y2="9" stroke="#fff" stroke-width="1.2"/></svg></div>
    </div>
    <div class="about" style="top:251px"><h3>What is 38-38?</h3><p>Lorem ipsum dolor sit amet, consectetur adipiscing elit, sed do eiusmod tempor incididunt ut labore et dolore magna aliqua. Ut enim ad minim veniam, quis nostrud exercitation ullamco laboris nisi ut aliquip ex ea commodo consequat. Duis aute irure dolor in reprehenderit in voluptate velit esse cillum dolore eu fugiat nulla pariatur.</p></div>
    <footer class="footer"><span class="copy">Copyright NORVELD 2010, all rights reserved &nbsp;|&nbsp; B2B Service</span><span class="mark"><i></i>www.4747.be</span><span class="legal">Help &nbsp;|&nbsp; Terms of Use &nbsp;|&nbsp; Respect for privacy</span></footer>
  </section>

  <!-- Reverse -->
  <section class="screen" style="left:70px;top:1183px;height:388px">
    <header class="navbar">
      <div class="brand">38-38</div>
      <nav class="nav-links" style="left:281px"><span>People</span><span>Companies</span><span class="active">Reverse</span><span>International</span></nav>
      <div class="lang"><i></i>English<b>⌄</b></div>
    </header>
    <div class="hero"></div>
    <div class="hero-art" role="img" aria-label="Illustration of a phone directory and a delivery van with map pins"></div>
    <h2 class="hero-title">The ONE number for ALL<br>directory enquiries</h2>
    <p class="hero-sub">Number (the one for which you are looking for the owner)</p>
    <div class="search-card short">
      <div class="field" style="left:12px;top:12px;width:239px">Number</div>
      <div class="btn" style="left:12px;top:36px;width:239px">38-38! <svg viewBox="0 0 10 10"><circle cx="5.5" cy="4.5" r="3.2" fill="none" stroke="#fff" stroke-width="1.2"/><line x1="3.2" y1="6.8" x2="1" y2="9" stroke="#fff" stroke-width="1.2"/></svg></div>
    </div>
    <div class="about" style="top:251px"><h3>What is 38-38?</h3><p>Lorem ipsum dolor sit amet, consectetur adipiscing elit, sed do eiusmod tempor incididunt ut labore et dolore magna aliqua. Ut enim ad minim veniam, quis nostrud exercitation ullamco laboris nisi ut aliquip ex ea commodo consequat. Duis aute irure dolor in reprehenderit in voluptate velit esse cillum dolore eu fugiat nulla pariatur.</p></div>
    <footer class="footer"><span class="copy">Copyright NORVELD 2010, all rights reserved &nbsp;|&nbsp; B2B Service</span><span class="mark"><i></i>www.4747.be</span><span class="legal">Help &nbsp;|&nbsp; Terms of Use &nbsp;|&nbsp; Respect for privacy</span></footer>
  </section>

  <!-- Search results -->
  <section class="screen" style="left:680px;top:348px;height:547px">
    <header class="navbar">
      <div class="brand">38-38</div>
      <nav class="nav-links" style="left:281px"><span class="active">People</span><span>Companies</span><span>Reverse</span><span>International</span></nav>
      <div class="lang"><i></i>English<b>⌄</b></div>
    </header>
    <div class="hero"></div>
    <div class="hero-art" role="img" aria-label="Illustration of a phone directory and a delivery van with map pins"></div>
    <h2 class="hero-title">The ONE number for ALL<br>directory enquiries</h2>
    <p class="hero-sub">Find people, contact info &amp; background checks</p>
    <div class="search-card">
      <div class="field filled" style="left:12px;top:12px;width:116px">Marlet<svg class="clear" viewBox="0 0 10 10"><circle cx="5" cy="5" r="4" fill="none" stroke="#333"/><path d="M3.5 3.5l3 3M6.5 3.5l-3 3" stroke="#333"/></svg></div>
      <div class="field filled" style="left:135px;top:12px;width:116px">Pierre<svg class="clear" viewBox="0 0 10 10"><circle cx="5" cy="5" r="4" fill="none" stroke="#333"/><path d="M3.5 3.5l3 3M6.5 3.5l-3 3" stroke="#333"/></svg></div>
      <div class="field filled" style="left:12px;top:37px;width:239px">Rue des Tilleuls 42<svg class="clear" viewBox="0 0 10 10"><circle cx="5" cy="5" r="4" fill="none" stroke="#333"/><path d="M3.5 3.5l3 3M6.5 3.5l-3 3" stroke="#333"/></svg></div>
      <div class="btn" style="left:12px;top:61px;width:239px">38-38! <svg viewBox="0 0 10 10"><circle cx="5.5" cy="4.5" r="3.2" fill="none" stroke="#fff" stroke-width="1.2"/><line x1="3.2" y1="6.8" x2="1" y2="9" stroke="#fff" stroke-width="1.2"/></svg></div>
    </div>
    <p class="found" style="top:248px"><b>38-38</b> &nbsp;found &nbsp;<b>1</b> &nbsp;possible result(s) for &nbsp;<b>Marlet Pierre</b></p>
    <div class="result" style="top:271px">
      <div class="row"><span>Name</span>Marlet Pierre Van Aken Sofie</div>
      <div class="row"><span>Address</span>Rue des Tilleuls 42</div>
      <div class="row"><span>State / City</span>B-1190 Vorst</div>
      <div class="row"><span>Phone numbers</span>02-555-01-77</div>
      <div class="row"><span>Location</span><a>See Location on Mapvista</a></div>
    </div>
    <div class="about" style="top:415px"><h3>What is 38-38!?</h3><p>Lorem ipsum dolor sit amet, consectetur adipiscing elit, sed do eiusmod tempor incididunt ut labore et dolore magna aliqua. Ut enim ad minim veniam, quis nostrud exercitation ullamco laboris nisi ut aliquip ex ea commodo consequat. Duis aute irure dolor in reprehenderit in voluptate velit esse cillum dolore eu fugiat nulla pariatur.</p></div>
    <footer class="footer"><span class="copy">Copyright NORVELD 2010, all rights reserved &nbsp;|&nbsp; B2B Service</span><span class="mark"><i></i>www.4747.be</span><span class="legal">Help &nbsp;|&nbsp; Terms of Use &nbsp;|&nbsp; Respect for privacy</span></footer>
  </section>

  <!-- Search results, scrolled -->
  <section class="screen" style="left:680px;top:935px;height:375px">
    <header class="navbar">
      <div class="brand">38-38</div>
      <nav class="nav-links" style="left:281px"><span class="active">People</span><span>Companies</span><span>Reverse</span><span>International</span></nav>
      <div class="lang"><i></i>English<b>⌄</b></div>
    </header>
    <div class="sticky">
      <div class="field" style="left:68px;top:12px;width:116px;height:16px">First Name</div>
      <div class="field" style="left:192px;top:12px;width:116px;height:16px">Last Name</div>
      <div class="field" style="left:316px;top:12px;width:115px;height:16px">Locality</div>
      <div class="btn" style="left:439px;top:12px;width:77px">38-38! <svg viewBox="0 0 10 10"><circle cx="5.5" cy="4.5" r="3.2" fill="none" stroke="#fff" stroke-width="1.2"/><line x1="3.2" y1="6.8" x2="1" y2="9" stroke="#fff" stroke-width="1.2"/></svg></div>
    </div>
    <p class="found" style="top:75px"><b>38-38</b> &nbsp;found &nbsp;<b>1</b> &nbsp;possible result(s) for &nbsp;<b>Marlet Pierre</b></p>
    <div class="result" style="top:98px">
      <div class="row"><span>Name</span>Marlet Pierre Van Aken Sofie</div>
      <div class="row"><span>Address</span>Rue des Tilleuls 42</div>
      <div class="row"><span>State / City</span>B-1190 Vorst</div>
      <div class="row"><span>Phone numbers</span>02-555-01-77</div>
      <div class="row"><span>Location</span><a>See Location on Mapvista</a></div>
    </div>
    <div class="about" style="top:243px"><h3>What is 38-38?</h3><p>Lorem ipsum dolor sit amet, consectetur adipiscing elit, sed do eiusmod tempor incididunt ut labore et dolore magna aliqua. Ut enim ad minim veniam, quis nostrud exercitation ullamco laboris nisi ut aliquip ex ea commodo consequat. Duis aute irure dolor in reprehenderit in voluptate velit esse cillum dolore eu fugiat nulla pariatur.</p></div>
    <footer class="footer"><span class="copy">Copyright NORVELD 2010, all rights reserved &nbsp;|&nbsp; B2B Service</span><span class="mark"><i></i>www.4747.be</span><span class="legal">Help &nbsp;|&nbsp; Terms of Use &nbsp;|&nbsp; Respect for privacy</span></footer>
  </section>

  <!-- International -->
  <section class="screen" style="left:1284px;top:328px;height:1012px">
    <header class="navbar">
      <div class="brand">38-38</div>
      <nav class="nav-links" style="left:280px"><span>People</span><span>Companies</span><span>Reverse</span><span class="active">International</span></nav>
      <div class="lang"><i></i>English<b>⌄</b></div>
    </header>
    <div class="hero"></div>
    <h2 class="intl-title">38-38 Experience Eperators<br>Will Help You And Find You<br>The Desired Number</h2>
    <div class="art" role="img" aria-label="Illustration of two operators beside a large browser window showing a search" style="left:316px;top:57px;width:200px;height:160px;background:linear-gradient(135deg,#fbc9cc,#f6f6fb 45%,#e84b52 85%)"></div>
    <div class="art" role="img" aria-label="Illustration of a person browsing contact cards on a large phone screen" style="left:51px;top:262px;width:195px;height:152px;background:linear-gradient(160deg,#f2f2f2,#e4e4e4 60%,#f6d3d5)"></div>
    <p class="intl-text" style="left:251px;top:309px">Whether looking for the number of a hotel in Benidorm, that of the tourist office in Saint-Tropez or that of a friend living in Italy, or even to find a supplier located in London or Amsterdam, the 38-38 also allows you to search for a telephone or fax number abroad*, whether it is an individual, a company or an administration, etc.</p>
    <p class="intl-text" style="left:60px;top:496px">With 38-38, you no longer need to know the call number for national information, the call number for the reverse directory and then the call number for international information, because 38-38 is really the service of all telephone inquiries.</p>
    <div class="art" role="img" aria-label="Illustration of a thinking person framed by a red award rosette" style="left:336px;top:452px;width:180px;height:140px;background:linear-gradient(150deg,#eeeeee,#f09a9d 55%,#d93a40)"></div>
    <div class="intl-band">
      <p class="intl-note" style="top:26px;font-size:8.5px;line-height:12.5px;font-weight:500;padding:0 95px">Finally, the 38-38 being offered at a single price, whatever the type of search, the international is therefore offered at the same very attractive price as the national, which is unique in Europe!</p>
      <div class="map" role="img" aria-label="Coloured map of Europe highlighting the available countries"></div>
      <p class="intl-note" style="top:294px;font-size:6.5px;line-height:12.5px">* Countries available: Denmark, Spain, France, Great Britain, Italy, Luxembourg, Norway and the Netherlands.<br>Initially, this service will be available 7 days a week, between 8 a.m. and 9 p.m.</p>
    </div>
    <footer class="footer"><span class="copy">Copyright NORVELD 2010, all rights reserved &nbsp;|&nbsp; B2B Service</span><span class="mark"><i></i>www.4747.be</span><span class="legal">Help &nbsp;|&nbsp; Terms of Use &nbsp;|&nbsp; Respect for privacy</span></footer>
  </section>

  <p class="outro">Please contact me if you need design improvement.<br>Thank you.</p>
</main>
</body>
</html>
```